Brightfen Business Card Redesign & Logo Update

We need to update our business cards to something more modern and fresh. Brightfen can provide the current color schemes and old design examples, but welcome creativity in helping us with this redesign. PLEASE NOTE that we no longer utilize the "tree" and/or "leaf" imagery in our branding. If able would apprecaite an update on the quality of our "words only" logo in Ai. / PNG formats too.

Target Market(s)

Investors, landowners, corporate partners, contractors

Industry/Entity Type

Environmental Restoration & Conservation

Contact Information for Business Card

Logo, persons name, title, mailing address, phone and email, website url

Font styles to use
Other font styles liked:
• Merriweather

Requirements
Nice to have
• Logo, persons name, title, mailing address, phone and email, website url, but open to ideams
Should not have
• No all back backgrounds

```html
<!DOCTYPE html>
<html lang="en">
<head>
<meta charset="utf-8">
<title>Brightfen Business Card</title>
<link rel="stylesheet" href="https://fonts.googleapis.com/css2?family=Merriweather:wght@400;700;900&display=swap">
<style>
  :root {
    --bg: #e4e4e4;
    --card: #ffffff;
    --orange: #ee7f22;
    --green: #177a3a;
    --ink: #1f1f1f;
  }
  * { margin: 0; padding: 0; box-sizing: border-box; }
  html, body {
    width: 1146px;
    height: 1200px;
    overflow: hidden;
    background: var(--bg);
    font-family: "Merriweather", Georgia, serif;
    color: var(--ink);
  }
  .canvas { position: relative; width: 1146px; height: 1200px; }
  .card {
    position: absolute;
    left: 176px;
    width: 797px;
    height: 455px;
    background: var(--card);
    overflow: hidden;
  }
  .card--front { top: 113px; }
  .card--back { top: 596px; height: 467px; }

  .wordmark { text-align: center; }
  .wordmark__name {
    font-weight: 900;
    color: var(--green);
    letter-spacing: 3px;
    line-height: 1;
  }
  .wordmark__tagline {
    font-weight: 700;
    text-transform: uppercase;
    color: var(--ink);
    line-height: 1;
  }
  .card--front .wordmark {
    position: absolute;
    left: 0; right: 0;
    top: 180px;
  }
  .card--front .wordmark__name { font-size: 74px; }
  .card--front .wordmark__tagline { font-size: 17px; letter-spacing: 1.2px; margin-top: 16px; }

  .contact {
    position: absolute;
    left: 37px;
    top: 86px;
  }
  .contact__name { font-size: 26px; font-weight: 700; letter-spacing: 0.5px; text-transform: uppercase; }
  .contact__first { color: var(--orange); }
  .contact__last { color: var(--green); }
  .contact__title { font-size: 21px; margin-top: 6px; }
  .contact__address { font-size: 21px; line-height: 31px; margin-top: 22px; }
  .contact__lines { list-style: none; margin-top: 20px; font-size: 21px; line-height: 28px; }
  .contact__lines li { display: flex; align-items: center; gap: 8px; }
  .contact__icon { width: 15px; height: 15px; flex: none; }

  .divider {
    position: absolute;
    left: 387px;
    top: 92px;
    width: 2px;
    height: 239px;
    background: var(--orange);
  }
  .card--back .wordmark {
    position: absolute;
    left: 417px;
    width: 332px;
    top: 186px;
  }
  .card--back .wordmark__name { font-size: 48px; letter-spacing: 2px; }
  .card--back .wordmark__tagline { font-size: 13px; letter-spacing: 0.4px; margin-top: 10px; }

  .waves { position: absolute; left: 0; bottom: 0; width: 797px; height: 110px; }
</style>
</head>
<body>
<main class="canvas">
  <section class="card card--front" aria-label="Card front">
    <div class="wordmark">
      <div class="wordmark__name">BRIGHTFEN</div>
      <div class="wordmark__tagline">Environmental Credit Company</div>
    </div>
  </section>

  <section class="card card--back" aria-label="Card back">
    <div class="contact">
      <p class="contact__name"><span class="contact__first">Marcus</span> <span class="contact__last">Hale</span></p>
      <p class="contact__title">Founder</p>
      <p class="contact__address">Your Company Address<br>Road No. 48, PO 2100, BD</p>
      <ul class="contact__lines">
        <li>
          <svg class="contact__icon" viewBox="0 0 16 16" aria-hidden="true"><path fill="#ee7f22" d="M3 1.5l3 .5 1 3.2-1.7 1.3a9 9 0 0 0 4.2 4.2l1.3-1.7 3.2 1 .5 3c-.2.9-1 1.5-2 1.5A12.5 12.5 0 0 1 1.5 3.5c0-1 .6-1.8 1.5-2z"/></svg>
          (555) 214-3890
        </li>
        <li>
          <svg class="contact__icon" viewBox="0 0 16 16" aria-hidden="true"><rect x="1" y="3" width="14" height="10" rx="1" fill="#ee7f22"/><path d="M1.5 3.8L8 9l6.5-5.2" fill="none" stroke="#fff" stroke-width="1.4"/></svg>
          hello@brightfenmail.com
        </li>
        <li>
          <svg class="contact__icon" viewBox="0 0 16 16" aria-hidden="true"><circle cx="8" cy="8" r="7" fill="#ee7f22"/><path d="M1 8h14M8 1c-2.5 2.5-2.5 11.5 0 14M8 1c2.5 2.5 2.5 11.5 0 14" fill="none" stroke="#fff" stroke-width="1"/></svg>
          www.brightfenrestore.com
        </li>
      </ul>
    </div>

    <div class="divider"></div>

    <div class="wordmark">
      <div class="wordmark__name">BRIGHTFEN</div>
      <div class="wordmark__tagline">Environmental Credit Company</div>
    </div>

    <svg class="waves" viewBox="0 357 797 110" preserveAspectRatio="none" aria-hidden="true">
      <path fill="#ee7f22" d="M0,392 C150,365 300,370 430,398 C540,420 660,418 797,406 L797,467 L0,467 Z"/>
      <path fill="#177a3a" stroke="#ffffff" stroke-width="5" d="M0,436 C150,424 300,416 430,422 C560,430 680,438 797,420 L800,470 L-3,470 Z"/>
    </svg>
  </section>
</main>
</body>
</html>
```